Personal training and nutrition business needs business card design

We need a business card that outlays our services and invites potential customers to join our team and take the first step to a healthier and more enjoyable life. We cater for any level of fitness and specialize in weight loss and conditioning, strength training, muscle gain and strength endurance. Whether you are just starting off or need some help getting to the next level of your journey we are here to get the job done.
We specialize in one on one or one on two personal training sessions and each program will be custom made to suit individual fitness goals of our clients

```html
<!DOCTYPE html>
<html lang="en">
<head>
<meta charset="utf-8">
<title>Pulse &amp; Stride – Business Card</title>
<link rel="stylesheet" href="https://fonts.googleapis.com/css2?family=Arimo:wght@400;700&family=Oswald:wght@500&display=swap">
<style>
  :root {
    --stage: #2b2b2d;
    --card: #1c1d20;
    --card-back: #141416;
    --purple: #8e4fb0;
    --purple-light: #b05cb8;
    --white: #ffffff;
    --grey: #c9c9cc;
    --rule: #8a8a8e;
  }
  * { margin: 0; padding: 0; box-sizing: border-box; }
  html, body { width: 1200px; height: 1108px; overflow: hidden; }
  body {
    background: var(--stage);
    font-family: "Arimo", Arial, sans-serif;
    position: relative;
  }
  .card {
    position: absolute;
    top: 204px;
    width: 420px;
    height: 700px;
    border-radius: 26px;
    box-shadow: 0 18px 40px rgba(0,0,0,.45);
  }
  .card--front {
    left: 150px;
    background: var(--card);
    display: flex;
    flex-direction: column;
    align-items: center;
    text-align: center;
    padding-top: 120px;
  }
  .card--back {
    left: 630px;
    background: var(--card-back);
    overflow: hidden;
  }
  .brand-name {
    font-weight: 700;
    font-size: 44px;
    line-height: 1.05;
    color: var(--white);
    letter-spacing: 1px;
    text-transform: uppercase;
  }
  .brand-mark {
    width: 34px; height: 34px;
    background: var(--purple);
    border-radius: 4px;
    margin-bottom: 22px;
  }
  .tagline {
    margin-top: 14px;
    font-family: "Oswald", "Arial Narrow", sans-serif;
    font-size: 14px;
    letter-spacing: 1.5px;
    color: var(--purple);
  }
  .person-name {
    margin-top: 44px;
    font-size: 27px;
    color: var(--purple);
    text-transform: uppercase;
    letter-spacing: .5px;
  }
  .person-role {
    margin-top: 4px;
    font-size: 20px;
    color: var(--grey);
  }
  .contact-icons {
    display: flex;
    align-items: center;
    gap: 6px;
    margin-top: 20px;
    width: 300px;
  }
  .contact-icons .rule { flex: 1; height: 1px; background: var(--rule); }
  .icon {
    width: 30px; height: 30px;
    background: var(--purple);
    border-radius: 4px;
    display: flex; align-items: center; justify-content: center;
  }
  .contact-list {
    margin-top: 14px;
    font-size: 20px;
    line-height: 1.3;
    color: var(--grey);
  }
  .divider {
    width: 300px; height: 1px;
    background: var(--rule);
    margin: 16px 0;
  }
  .address {
    font-size: 20px;
    line-height: 1.3;
    color: var(--grey);
  }
  .back-pattern {
    position: absolute; inset: 0;
    background: linear-gradient(160deg, #3a3a3e 0%, #222225 45%, #111113 100%);
  }
  .back-brand {
    position: absolute;
    right: 70px; bottom: 150px;
    font-weight: 700;
    font-size: 16px;
    color: var(--purple);
    text-transform: uppercase;
    letter-spacing: 1px;
  }
</style>
</head>
<body>
  <section class="card card--front">
    <div class="brand-mark"></div>
    <h1 class="brand-name">Pulse &amp;<br>Stride</h1>
    <p class="tagline">PERSONAL TRAINING. NUTRITION. MOTIVATION</p>
    <h2 class="person-name">Marcus Lee</h2>
    <p class="person-role">Managing Director</p>
    <div class="contact-icons">
      <span class="rule"></span>
      <span class="icon" aria-label="Phone">
        <svg width="18" height="18" viewBox="0 0 24 24"><path fill="#1c1d20" d="M6.6 10.8a15 15 0 0 0 6.6 6.6l2.2-2.2a1 1 0 0 1 1-.25 11.4 11.4 0 0 0 3.6.57 1 1 0 0 1 1 1V20a1 1 0 0 1-1 1A17 17 0 0 1 3 4a1 1 0 0 1 1-1h3.5a1 1 0 0 1 1 1c0 1.25.2 2.45.57 3.57a1 1 0 0 1-.25 1z"/></svg>
      </span>
      <span class="icon" aria-label="Email">
        <svg width="18" height="18" viewBox="0 0 24 24"><rect x="3" y="5" width="18" height="14" rx="1" fill="none" stroke="#1c1d20" stroke-width="2"/><path d="M3 6l9 7 9-7" fill="none" stroke="#1c1d20" stroke-width="2"/></svg>
      </span>
      <span class="icon" aria-label="Website">
        <svg width="18" height="18" viewBox="0 0 24 24"><circle cx="12" cy="12" r="9" fill="none" stroke="#1c1d20" stroke-width="2"/><path d="M3 12h18M12 3c3 3 3 15 0 18M12 3c-3 3-3 15 0 18" fill="none" stroke="#1c1d20" stroke-width="1.6"/></svg>
      </span>
      <span class="rule"></span>
    </div>
    <div class="contact-list">
      <p>044-987 654 321</p>
      <p>hello@pulsestride.com</p>
      <p>www.pulsestride.com</p>
    </div>
    <div class="divider"></div>
    <div class="address">
      <p>17, Elm Street Suite 4</p>
      <p>30218, Northland</p>
    </div>
  </section>

  <section class="card card--back">
    <div class="back-pattern" role="img" aria-label="Repeating glossy brand-mark pattern on black"></div>
    <p class="back-brand">Pulse &amp; Stride</p>
  </section>
</body>
</html>
```